Brookvale Building Company - advertisement poster

I am looking to print some canvas signs to advertise my general contracting company, Brookvale Building Company. The sign will measure 6' long x 3' high so the size should match that ratio. I already have a logo icon, which is the Letter 'B' and some trees that I would like to incorporate, see attached. I would also like the to have the following information listed:
1) phone number: 831-555-0172
2) email: brookvalebuildingcompany@mailnest.example
3) website: brookvalebuildingcompany.example
4) Lic#4826130
5) I want to use this text: "BUILD WITH THE B-CREW!"

The ad should be relatively simple and clean. Black and Green are my company colors. I am open to creative ideas!

Target Market(s)

People looking to renovate their homes

Industry/Entity Type

Construction

Colors
59FF00
82FF00
B8FF75
E3FFCB
F4FFEA

Requirements
Must have
• Must have my company logo
Should not have
• No photos or complex graphics

```html
<!DOCTYPE html>
<html lang="en">
<head>
<meta charset="utf-8">
<title>Brookvale Building Company – Sign</title>
<link rel="stylesheet" href="https://fonts.googleapis.com/css2?family=Source+Sans+3:wght@600;700;900&display=swap">
<style>
  :root {
    --black: #000000;
    --green: #6ab232;
    --navy: #171e63;
    --white: #ffffff;
    --mist-light: #ffffff;
    --mist-dark: #c0c1d6;
    --page: #ffffff;
  }
  html, body {
    margin: 0;
    width: 1200px;
    height: 927px;
    overflow: hidden;
    background: var(--page);
    font-family: "Source Sans 3", "Myriad Pro", Arial, sans-serif;
  }
  .canvas {
    position: relative;
    width: 1200px;
    height: 927px;
  }
  .sign {
    position: absolute;
    left: 47px;
    top: 143px;
    width: 1112px;
    height: 557px;
    outline: 1px solid var(--black);
  }
  .sign-shapes {
    position: absolute;
    inset: 0;
    width: 100%;
    height: 100%;
    display: block;
  }
  .sign-text {
    position: absolute;
    margin: 0;
    text-align: center;
    white-space: nowrap;
  }

  /* left panel */
  .brand {
    left: 70px;
    width: 320px;
    top: 60px;
    display: flex;
    flex-direction: column;
    align-items: center;
    gap: 16px;
  }
  .brand-square {
    width: 96px;
    height: 96px;
    background: var(--green);
  }
  .brand-name {
    color: var(--white);
    font-weight: 700;
    line-height: 1.05;
    letter-spacing: 3px;
    text-transform: uppercase;
  }
  .brand-name .line-main { display: block; font-size: 50px; }
  .brand-name .line-sub { display: block; font-size: 24px; letter-spacing: 7px; margin-top: 6px; }

  .phone {
    left: 20px;
    width: 420px;
    top: 336px;
    color: var(--white);
    font-weight: 700;
    font-size: 56px;
    letter-spacing: 1px;
    line-height: 1;
  }
  .license {
    left: 20px;
    width: 420px;
    top: 456px;
    color: var(--white);
    font-weight: 700;
    font-size: 25px;
    line-height: 1;
  }

  /* right panel */
  .headline {
    left: 500px;
    width: 580px;
    top: 78px;
    color: var(--black);
    font-weight: 900;
    line-height: 1;
    paint-order: stroke fill;
    -webkit-text-stroke: 2px var(--white);
  }
  .headline .line-top { display: block; font-size: 78px; letter-spacing: -1px; }
  .headline .line-crew { display: block; font-size: 98px; margin-top: 10px; letter-spacing: -1px; }

  .contact-label,
  .contact-value {
    left: 500px;
    width: 580px;
    color: var(--navy);
    font-weight: 700;
    line-height: 1;
  }
  .contact-label { font-size: 26px; }
  .contact-value { font-size: 25px; }
  .email-label { top: 284px; }
  .email-value { top: 316px; }
  .website-label { top: 393px; }
  .website-value { top: 432px; }

  .contact-rule {
    position: absolute;
    left: 537px;
    top: 370px;
    width: 497px;
    height: 4px;
    background: var(--green);
  }
</style>
</head>
<body>
  <main class="canvas">
    <section class="sign">
      <svg class="sign-shapes" viewBox="0 0 2025 1013" preserveAspectRatio="none" aria-hidden="true">
        <defs>
          <linearGradient id="mist" x1="0" y1="1" x2="1" y2="0">
            <stop offset="0.3" stop-color="var(--mist-light)"/>
            <stop offset="1" stop-color="var(--mist-dark)"/>
          </linearGradient>
        </defs>
        <rect class="backdrop" x="0" y="0" width="2025" height="1013" fill="url(#mist)"/>
        <polygon class="panel-dark" points="0,0 742,0 925,937 100,1013 0,508" fill="var(--black)"/>
        <polygon class="edge-stripe" points="0,508 100,1013 77,1013 0,620" fill="var(--green)"/>
        <polygon class="edge-corner" points="0,620 77,1013 0,1013" fill="var(--white)"/>
        <polygon class="base-navy" points="100,1013 925,937 939,1013" fill="var(--navy)"/>
        <polygon class="base-green" points="925,937 2025,837 2025,1013 939,1013" fill="var(--green)"/>
      </svg>

      <div class="sign-text brand">
        <span class="brand-square" aria-hidden="true"></span>
        <p class="brand-name">
          <span class="line-main">Brookvale</span>
          <span class="line-sub">Building Company</span>
        </p>
      </div>

      <p class="sign-text phone">831-555-0172</p>
      <p class="sign-text license">Lic#4826130</p>

      <h1 class="sign-text headline">
        <span class="line-top">BUILD WITH THE</span>
        <span class="line-crew">B-CREW</span>
      </h1>

      <p class="sign-text contact-label email-label">email:</p>
      <p class="sign-text contact-value email-value">brookvalebuildingcompany@mailnest.example</p>
      <span class="contact-rule" aria-hidden="true"></span>
      <p class="sign-text contact-label website-label">website:</p>
      <p class="sign-text contact-value website-value">brookvalebuildingcompany.example</p>
    </section>
  </main>
</body>
</html>
```